Card front cover, made up of words and statements, similar to the front of a tovarique bag.

I'm looking to design the front of a card or post card I will use in my business. I want to use a mash up of words and statements and sentences to inspire my audience. The card should be visually nice and use various fonts. My business inspires kids to set goals and dream big. You can use the "moon" shape as seen in my logo, but stick to mostly the words and statements listed on the attached word document or other similar statements you find, the shorter statements tend to look better. I'm interested to see a use of different fonts and sizes. All with a "modern" look and feel.

Target Market(s)

parents of children ages 8-12

Industry/Entity Type

Party space: specifically slumber parties

Font styles to use
Other font styles liked:
• Avenir Next LT pro

Colors
FFC000
F8CF3A
FAE287
FDF2CF
FEFAEE

Requirements
Must have
• The use of the "moon" logo and the words: Sleep Less, Dream More
Nice to have
• I made a long list of inspirational quotes to use, they don't all need to be used but that is the idea I'm looking for. After looking at designs the long sentences do NOT work as well. Please either shorten them or find other similar statements.
Should not have
• color, please use the yellow as shown in my moon logo, black and white

```html
<!DOCTYPE html>
<html lang="en">
<head>
<meta charset="utf-8">
<title>Sleep Less, Dream More – Card Front</title>
<link rel="stylesheet" href="https://fonts.googleapis.com/css2?family=Alegreya+Sans:wght@400&family=Arimo:wght@400;700&family=Crimson+Pro:wght@800&family=Playfair+Display:wght@900&family=Tinos:wght@400;700&display=swap">
<style>
  :root {
    --ink: #333333;
    --sun-deep: #FDCF22;
    --sun-mid: #FFDA2E;
    --sun-light: #FFF45A;
    --paper: #FFFFFF;
    --label-yellow: #FFC000;
  }
  html, body {
    margin: 0;
    padding: 0;
    width: 1200px;
    height: 914px;
    overflow: hidden;
    background: var(--paper);
  }
  .card-front {
    display: block;
    width: 1200px;
    height: 914px;
  }
  .ink { fill: var(--ink); }
  .label-text { fill: var(--label-yellow); }
  .font-didone { font-family: "Playfair Display", "Didot", serif; font-weight: 900; }
  .font-grotesk { font-family: "Arimo", "Helvetica", Arial, sans-serif; font-weight: 400; }
  .font-grotesk-bold { font-family: "Arimo", "Helvetica", Arial, sans-serif; font-weight: 700; }
  .font-roman { font-family: "Tinos", "Times New Roman", serif; font-weight: 400; }
  .font-roman-bold { font-family: "Tinos", "Times New Roman", serif; font-weight: 700; }
  .font-humanist { font-family: "Alegreya Sans", "Candara", sans-serif; font-weight: 400; }
  .font-condensed-serif { font-family: "Crimson Pro", "Georgia", serif; font-weight: 800; }
  .rule { stroke: var(--ink); stroke-width: 1.2; }
</style>
</head>
<body>
<svg class="card-front" viewBox="0 0 1200 914" xmlns="http://www.w3.org/2000/svg" role="img" aria-label="Card front: a mash-up of inspirational dream statements on yellow">
  <defs>
    <linearGradient id="sun-wash" x1="0" y1="0" x2="1" y2="1">
      <stop offset="0" stop-color="var(--sun-deep)"/>
      <stop offset="0.55" stop-color="var(--sun-mid)"/>
      <stop offset="1" stop-color="var(--sun-light)"/>
    </linearGradient>
  </defs>

  <!-- yellow panel -->
  <rect class="panel" x="91" y="70" width="1019" height="764" fill="url(#sun-wash)"/>

  <!-- left column -->
  <g class="quote-realities ink font-roman-bold" font-size="27">
    <text x="119" y="127" textLength="488" lengthAdjust="spacingAndGlyphs">Never stop dreaming --- most realities</text>
    <text x="119" y="163" textLength="415" lengthAdjust="spacingAndGlyphs">were once created from dreams.</text>
  </g>

  <g class="label-swoon">
    <rect class="ink" x="113" y="182" width="490" height="59"/>
    <text class="label-text font-grotesk-bold" x="134" y="226" font-size="31" textLength="453" lengthAdjust="spacingAndGlyphs">SWOON, SLUMBER, REPEAT</text>
  </g>

  <g class="quote-goals ink font-didone" font-size="68">
    <text x="125" y="308" textLength="468" lengthAdjust="spacingAndGlyphs">Goals are just</text>
    <text x="125" y="380" textLength="415" lengthAdjust="spacingAndGlyphs">dreams with</text>
    <text x="125" y="449" textLength="350" lengthAdjust="spacingAndGlyphs">a deadline</text>
  </g>

  <g class="quote-stairs ink font-grotesk" font-size="30">
    <text x="125" y="492" textLength="460" lengthAdjust="spacingAndGlyphs">There is no elevator to success,</text>
    <text x="166" y="528" textLength="378" lengthAdjust="spacingAndGlyphs">you have to take the stairs</text>
  </g>

  <text class="quote-fail ink font-grotesk" font-size="34" transform="translate(651 529) rotate(-90)" textLength="431" lengthAdjust="spacingAndGlyphs">You only fail when you stop</text>

  <!-- right column -->
  <g class="quote-chase-small ink font-roman" font-size="31">
    <text x="678" y="125" textLength="355" lengthAdjust="spacingAndGlyphs">DON'T FOLLOW YOUR</text>
    <text x="678" y="162" textLength="345" lengthAdjust="spacingAndGlyphs">DREAM CHASE THEM!</text>
  </g>
  <line class="rule" x1="681" y1="175" x2="1046" y2="175"/>

  <g class="prompt-action ink font-humanist" font-size="22">
    <text x="678" y="201" textLength="337" lengthAdjust="spacingAndGlyphs">What's one action I can take today</text>
    <text x="678" y="227" textLength="370" lengthAdjust="spacingAndGlyphs">to make my goal feel more achievable?</text>
  </g>

  <g class="headline-sleep ink font-didone" font-size="62">
    <text x="682" y="296" textLength="342" lengthAdjust="spacingAndGlyphs">Sleep Less,</text>
    <text x="682" y="354" textLength="348" lengthAdjust="spacingAndGlyphs">Dream More</text>
  </g>
  <line class="rule" x1="682" y1="364" x2="1046" y2="364"/>

  <text class="quote-wish ink font-roman" x="687" y="403" font-size="40" textLength="365" lengthAdjust="spacingAndGlyphs">Dream it, wish it, do it</text>

  <g class="label-energy">
    <rect class="ink" x="673" y="417" width="378" height="32"/>
    <text class="label-text font-roman-bold" x="686" y="439" font-size="16" textLength="352" lengthAdjust="spacingAndGlyphs">BE THE ENERGY YOU WANT TO ATTRACT</text>
  </g>

  <g class="prompt-motivates ink font-grotesk" font-size="28">
    <text x="678" y="486" textLength="352" lengthAdjust="spacingAndGlyphs">What motivates you to keep</text>
    <text x="678" y="518" textLength="374" lengthAdjust="spacingAndGlyphs">going when things get tough?</text>
  </g>

  <text class="quote-never-stop ink font-roman" font-size="38" transform="translate(1090 518) rotate(-90)" textLength="420" lengthAdjust="spacingAndGlyphs">NEVER STOP DREAMING</text>

  <!-- lower band -->
  <g class="quote-chase-large ink font-didone" font-size="58">
    <text x="124" y="593" textLength="345" lengthAdjust="spacingAndGlyphs">Don't follow</text>
    <text x="123" y="662" textLength="346" lengthAdjust="spacingAndGlyphs">your dream</text>
    <text x="123" y="731" textLength="344" lengthAdjust="spacingAndGlyphs">chase them!</text>
  </g>
  <line class="rule" x1="483.5" y1="561" x2="483.5" y2="737" stroke-width="2"/>

  <g class="quote-people ink font-condensed-serif" font-size="40" text-anchor="end">
    <text x="906" y="592" textLength="405" lengthAdjust="spacingAndGlyphs">REMEMBER ANYTHING</text>
    <text x="906" y="639" textLength="405" lengthAdjust="spacingAndGlyphs">IS POSSIBLE WITH THE</text>
    <text x="906" y="688" textLength="320" lengthAdjust="spacingAndGlyphs">RIGHT PEOPLE TO</text>
    <text x="906" y="735" textLength="248" lengthAdjust="spacingAndGlyphs">SUPPORT YOU</text>
  </g>

  <text class="quote-right ink font-grotesk" x="124" y="800" font-size="56" textLength="795" lengthAdjust="spacingAndGlyphs">Do what is right, not what is easy</text>

  <text class="word-repeat ink font-grotesk" font-size="64" transform="translate(981 800) rotate(-90)" textLength="245" lengthAdjust="spacingAndGlyphs">REPEAT</text>

  <g class="label-dream-more">
    <rect class="ink" x="997" y="551" width="86" height="254"/>
    <text class="label-text font-roman-bold" font-size="32" transform="translate(1052 786) rotate(-90)" textLength="216" lengthAdjust="spacingAndGlyphs">Dream More</text>
  </g>
</svg>
</body>
</html>
```